Customer Value Leaflet

We need a bi-fold brochure designing, based on the attached PDF wireframes. Our company name is brambleharvik.com (of which the logo is currently being designed). The corporate colour is orange (the exact shade of which we are happy to leave to the designers discretion).

The leaflet will distributed to customer experience experts and marketers so the design needs to be bright, engaging, clean and simple. Design is critical.

It Company

```html
<!DOCTYPE html>
<html lang="en">
<head>
<meta charset="utf-8">
<title>Customer Value Leaflet – BrambleHarvik</title>
<link rel="stylesheet" href="https://fonts.googleapis.com/css2?family=Open+Sans:ital,wght@0,400;0,600;0,700;0,800;1,400;1,600&display=swap">
<style>
  :root {
    --orange: #f7941d;
    --orange-deep: #ef8a12;
    --ink: #111111;
    --grey: #c8c8c8;
    --grey-mid: #a9a9a9;
    --paper: #ffffff;
    --backdrop: #c9dbf8;
    --text: #222222;
  }
  * { box-sizing: border-box; margin: 0; padding: 0; }
  html, body { width: 1085px; height: 1200px; overflow: hidden; }
  body {
    background: var(--backdrop);
    font-family: "Open Sans", Arial, sans-serif;
    color: var(--text);
    position: relative;
  }
  .panel {
    position: absolute;
    width: 300px;
    height: 300px;
    background: var(--paper);
    overflow: hidden;
    box-shadow: 0 3px 8px rgba(40, 60, 100, 0.18);
  }

  /* Cover */
  .cover { background: var(--orange); color: var(--paper); text-align: center; }
  .cover .brand {
    position: absolute; left: 20px; top: 18px;
    font-weight: 700; font-size: 13px; color: var(--ink);
  }
  .cover .rule { position: absolute; height: 2px; background: var(--paper); }
  .cover .lead { position: absolute; left: 0; right: 0; top: 50px; font-size: 17px; }
  .cover .headline {
    position: absolute; left: 0; right: 0; top: 80px;
    font-weight: 800; font-size: 43px; line-height: 46px; letter-spacing: 0.5px;
  }
  .cover .tail { position: absolute; left: 0; right: 0; top: 218px; font-size: 17px; }

  /* Outside left: CLV */
  .clv-header {
    position: absolute; left: 0; top: 0; width: 100%; height: 30px;
    background: var(--grey); text-align: center; font-size: 12px; line-height: 30px; color: var(--text);
  }
  .clv-band { position: absolute; left: 0; top: 30px; width: 100%; height: 170px; background: var(--orange); }
  .clv-card { position: absolute; top: 40px; height: 52px; display: flex; }
  .clv-card .name {
    width: 24px; background: var(--ink); color: var(--paper);
    writing-mode: vertical-rl; transform: rotate(180deg);
    font-size: 10px; font-weight: 600; text-align: center;
  }
  .clv-card .value {
    width: 86px; background: var(--orange-deep); color: var(--paper);
    border: 3px solid var(--paper); border-left: none;
    font-size: 17px; line-height: 20px; padding: 4px 8px;
  }
  .clv-card.kim { left: 10px; }
  .clv-card.kevin { left: 164px; }
  .clv-note {
    position: absolute; top: 112px; width: 120px;
    font-size: 11px; line-height: 13px; color: var(--paper); text-align: center;
  }
  .clv-note.kim { left: 14px; }
  .clv-note.kevin { left: 168px; }
  .clv-arrow { position: absolute; left: 128px; top: 30px; }
  .clv-arrow-label {
    position: absolute; left: 132px; top: 42px; width: 34px; height: 120px;
    writing-mode: vertical-rl; font-size: 10px; font-weight: 600;
    color: var(--text); text-align: center; letter-spacing: 0.3px;
  }
  .clv-pitch {
    position: absolute; left: 16px; right: 16px; top: 212px;
    font-size: 11px; line-height: 15px; color: var(--ink); text-align: center;
  }
  .clv-pitch strong { font-weight: 700; }

  /* Outside middle: platform */
  .platform { background: var(--orange); }
  .platform-copy {
    position: absolute; left: 14px; top: 20px; width: 150px;
    font-style: italic; font-size: 11px; line-height: 14px; color: var(--paper);
  }
  .platform-copy p + p { margin-top: 12px; }
  .platform-photo {
    position: absolute; left: 172px; top: 22px; width: 116px; height: 180px;
    background: linear-gradient(170deg, #e9e3df 0%, #c9b8ae 55%, #b2453f 100%);
  }
  .contact-band {
    position: absolute; left: 0; bottom: 0; width: 100%; height: 40px;
    background: var(--ink); color: var(--paper);
    font-size: 12px; font-weight: 700; line-height: 40px; text-align: center; word-spacing: 2px;
  }

  /* Inside left: personas */
  .persona-tab {
    position: absolute; top: 18px; width: 128px; height: 20px;
    background: var(--orange); color: var(--paper);
    font-size: 10px; font-weight: 600; line-height: 20px; text-align: center;
  }
  .persona-tab.kim { left: 16px; }
  .persona-tab.kevin { left: 156px; }
  .persona-figure {
    position: absolute; top: 50px; width: 40px; height: 64px; border-radius: 6px;
    background: linear-gradient(180deg, #d8d8d8, #9a9a9a);
  }
  .persona-figure.kim { left: 60px; }
  .persona-figure.kevin { left: 200px; }
  .persona-text {
    position: absolute; top: 126px; width: 128px;
    font-size: 10.5px; line-height: 13px; text-align: center; color: var(--ink);
  }
  .persona-text.kim { left: 16px; }
  .persona-text.kevin { left: 156px; }
  .orange-foot {
    position: absolute; left: 0; bottom: 0; width: 100%; height: 44px;
    background: var(--orange); color: var(--ink);
    font-size: 11px; line-height: 44px; text-align: center;
  }

  /* Inside middle: timeline */
  .timeline-arrow { position: absolute; left: 130px; top: 0; }
  .timeline-mark {
    position: absolute; left: 134px; width: 32px;
    writing-mode: vertical-rl; color: var(--paper);
    font-size: 9px; font-weight: 600; text-align: center;
  }
  .step {
    position: absolute; width: 118px;
    font-size: 10px; line-height: 12px; text-align: center; color: var(--ink);
  }
  .step.left { left: 8px; }
  .step.right { left: 174px; }
  .step-icon { position: absolute; }

  /* Inside right: closing */
  .closing-lead {
    position: absolute; left: 24px; top: 40px; width: 260px;
    font-size: 15px; font-weight: 700; line-height: 20px; color: var(--ink);
  }
  .closing-lead .term { color: var(--orange); text-decoration: underline; }
  .closing-claim {
    position: absolute; right: 22px; top: 108px; width: 240px;
    font-size: 14px; font-weight: 700; line-height: 19px; text-align: right; color: var(--ink);
  }
  .closing-link {
    position: absolute; left: 24px; top: 250px;
    font-size: 12px; color: var(--ink);
  }
  .closing-link strong { font-weight: 700; }
</style>
</head>
<body>

<!-- Folded leaflet, front -->
<section class="panel cover" style="left:392px; top:40px;">
  <div class="brand">[BrambleHarvik]</div>
  <div class="rule" style="left:40px; top:64px; width:60px;"></div>
  <div class="rule" style="left:200px; top:64px; width:60px;"></div>
  <div class="lead">We're a</div>
  <div class="headline">CUSTOMER<br>VALUE</div>
  <div class="rule" style="left:40px; top:230px; width:60px;"></div>
  <div class="rule" style="left:200px; top:230px; width:60px;"></div>
  <div class="tail">company</div>
</section>

<!-- Outside spread -->
<section class="panel clv" style="left:86px; top:390px;">
  <div class="clv-header">Once you can calculate CLV…</div>
  <div class="clv-band"></div>
  <svg class="clv-arrow" width="44" height="150" viewBox="0 0 44 150" aria-hidden="true">
    <polygon points="8,0 36,0 36,124 44,124 22,150 0,124 8,124" fill="#c8c8c8"/>
  </svg>
  <div class="clv-arrow-label">OPTIMISE YOUR MARKETING</div>
  <div class="clv-card kim"><div class="name">Kim</div><div class="value">CLV of £149</div></div>
  <div class="clv-card kevin"><div class="name">Kevin</div><div class="value">CLV of £282</div></div>
  <p class="clv-note kim">you can personalise Kim's marketing experience to grow her lifetime value to be more like Kevin's</p>
  <p class="clv-note kevin">you can understand why Kevin is more valuable and acquire more customers like him</p>
  <p class="clv-pitch">We use data and science to predict how your customers will behave in future. Even if you already use CLV we can help you do and earn more… <strong>brambleharvik.com</strong></p>
</section>

<section class="panel platform" style="left:392px; top:390px;">
  <div class="platform-copy">
    <p>Velora is our Customer Value Platform, designed for Marketers in the Digital Enterprise.</p>
    <p>Velora is like having a team of data scientists making valuable insights available to your website in real-time so you can deliver the ultimate customer experience.</p>
  </div>
  <div class="platform-photo" role="img" aria-label="Photo of visitors at a trade show stand"></div>
  <div class="contact-band">brambleharvik.com &nbsp;|&nbsp; 0845 000 3172</div>
</section>

<section class="panel cover" style="left:698px; top:390px;">
  <div class="brand">[BrambleHarvik]</div>
  <div class="rule" style="left:40px; top:64px; width:60px;"></div>
  <div class="rule" style="left:200px; top:64px; width:60px;"></div>
  <div class="lead">We're a</div>
  <div class="headline">CUSTOMER<br>VALUE</div>
  <div class="rule" style="left:40px; top:230px; width:60px;"></div>
  <div class="rule" style="left:200px; top:230px; width:60px;"></div>
  <div class="tail">company</div>
</section>

<!-- Inside spread -->
<section class="panel personas" style="left:86px; top:800px;">
  <div class="persona-tab kim">MEET KIM</div>
  <div class="persona-tab kevin">MEET KEVIN</div>
  <div class="persona-figure kim" role="img" aria-label="Illustration of Kim, a customer"></div>
  <div class="persona-figure kevin" role="img" aria-label="Illustration of Kevin, a customer"></div>
  <p class="persona-text kim">Kim has purchased 3 items from you over the past 3 months @ £109 margin and you acquired her though a Searchline PPC campaign</p>
  <p class="persona-text kevin">Kevin purchased an item last week @ £31 margin and you acquired him though a retargeting campaign</p>
  <div class="orange-foot">Right now you probably think Kim is your best customer…</div>
</section>

<section class="panel timeline" style="left:392px; top:800px;">
  <svg class="timeline-arrow" width="40" height="222" viewBox="0 0 40 222" aria-hidden="true">
    <polygon points="4,0 36,0 36,196 40,196 20,222 0,196 4,196" fill="#a9a9a9"/>
    <line x1="4" y1="64" x2="36" y2="64" stroke="#fff" stroke-width="2"/>
    <line x1="4" y1="132" x2="36" y2="132" stroke="#fff" stroke-width="2"/>
  </svg>
  <div class="timeline-mark" style="top:14px; height:44px;">+1 WEEK</div>
  <div class="timeline-mark" style="top:80px; height:44px;">+1 MONTH</div>
  <div class="timeline-mark" style="top:146px; height:50px;">+6 MONTHS</div>

  <p class="step left" style="top:10px;">Kim calls you to return an item…</p>
  <svg class="step-icon" style="left:56px; top:38px;" width="22" height="22" viewBox="0 0 22 22" aria-hidden="true"><circle cx="11" cy="11" r="10" fill="#a9a9a9"/></svg>
  <p class="step left" style="top:76px;">places 4 more online orders…</p>
  <svg class="step-icon" style="left:54px; top:104px;" width="26" height="22" viewBox="0 0 26 22" aria-hidden="true"><path d="M1 2h4l3 12h13l3-9H7" fill="none" stroke="#777" stroke-width="2"/><circle cx="10" cy="19" r="2" fill="#777"/><circle cx="19" cy="19" r="2" fill="#777"/></svg>
  <p class="step left" style="top:140px;">then places another order but doesn't come back for a month</p>
  <svg class="step-icon" style="left:56px; top:184px;" width="24" height="24" viewBox="0 0 24 24" aria-hidden="true"><polygon points="7,1 17,1 23,7 23,17 17,23 7,23 1,17 1,7" fill="#333"/></svg>

  <p class="step right" style="top:10px;">Kevin makes another purchase…</p>
  <svg class="step-icon" style="left:220px; top:38px;" width="26" height="22" viewBox="0 0 26 22" aria-hidden="true"><path d="M1 2h4l3 12h13l3-9H7" fill="none" stroke="#777" stroke-width="2"/><circle cx="10" cy="19" r="2" fill="#777"/><circle cx="19" cy="19" r="2" fill="#777"/></svg>
  <p class="step right" style="top:70px;">then 2 more (and even tweets about how great your service is)…</p>
  <svg class="step-icon" style="left:222px; top:110px;" width="22" height="22" viewBox="0 0 22 22" aria-hidden="true"><circle cx="11" cy="11" r="10" fill="#a9a9a9"/></svg>
  <p class="step right" style="top:140px;">and continues to make purchases on a bi-monthly basis</p>
  <svg class="step-icon" style="left:220px; top:180px;" width="26" height="22" viewBox="0 0 26 22" aria-hidden="true"><path d="M1 2h4l3 12h13l3-9H7" fill="none" stroke="#777" stroke-width="2"/><circle cx="10" cy="19" r="2" fill="#777"/><circle cx="19" cy="19" r="2" fill="#777"/></svg>

  <div class="orange-foot">but really it is Kevin.</div>
</section>

<section class="panel closing" style="left:698px; top:800px;">
  <p class="closing-lead">By predicting <span class="term">Customer Lifetime Value</span> today…</p>
  <p class="closing-claim">…you can optimise your business for tomorrow</p>
  <p class="closing-link">Find our more at <strong>www.brambleharvik.com</strong></p>
</section>

</body>
</html>
```